Residential Remodeling Contractor needs updated business card

I need a new design for my business card.
Name of the company is Ridgefell Construction. I need a card that commands presence, strength, integrity. I have been in business for 28 years. I am a Residential Remodeling Contractor that covers all aspects of a residential remodel and build.

```html
<!DOCTYPE html>
<html lang="en">
<head>
<meta charset="utf-8">
<title>Ridgefell Construction – Business Card</title>
<link rel="stylesheet" href="https://fonts.googleapis.com/css2?family=Cinzel:wght@600&family=Lato:wght@400;700&display=swap">
<style>
  :root {
    --brand-blue: #1f3d7f;
    --paper: #ffffff;
    --backdrop: #1c1c1c;
    --card-w: 580px;
    --card-h: 330px;
  }
  * { box-sizing: border-box; margin: 0; padding: 0; }
  html, body {
    width: 1200px; height: 1015px; overflow: hidden;
    background: var(--backdrop);
  }
  .canvas { position: relative; width: 1200px; height: 1015px; }

  .card {
    position: absolute;
    width: var(--card-w); height: var(--card-h);
    overflow: hidden;
  }

  /* Front side */
  .card--front {
    left: 70px; top: 140px;
    background: var(--brand-blue);
    color: var(--paper);
  }
  .brand-name {
    font-family: "Cinzel", serif;
    font-weight: 600;
    line-height: 1;
    letter-spacing: 1px;
  }
  .card--front .brand-name {
    position: absolute; left: 150px; top: 78px;
    font-size: 44px;
  }
  .brand-name .line-2 { display: block; padding-left: 26px; margin-top: 4px; }
  .since {
    position: absolute; left: 0; right: 0; top: 208px;
    text-align: center;
    font-family: "Cinzel", serif; font-weight: 600;
    font-size: 15px; letter-spacing: 1px;
  }
  .tagline {
    position: absolute; left: 0; right: 0; top: 262px;
    text-align: center;
    font-family: "Cinzel", serif; font-weight: 600;
    font-size: 15px; letter-spacing: 1.5px;
  }

  /* Back side */
  .card--back {
    left: 550px; top: 560px;
    background: var(--paper);
  }
  .band { position: absolute; inset: 0; }
  .card--back .brand-name {
    position: absolute; left: 150px; top: 34px;
    font-size: 38px;
    color: var(--brand-blue);
  }
  .person {
    position: absolute; left: 130px; top: 222px;
    font-family: "Lato", sans-serif; color: var(--paper);
  }
  .person__name { font-weight: 700; font-size: 19px; letter-spacing: 0.5px; }
  .person__role { font-size: 14px; margin-top: 2px; }
  .person__address { font-size: 14px; line-height: 1.35; margin-top: 14px; }

  .contact {
    position: absolute; right: 22px; top: 150px;
    list-style: none;
    font-family: "Lato", sans-serif; font-size: 14px;
    color: var(--paper); text-align: right; line-height: 1.5;
  }
  .contact li { display: flex; align-items: center; justify-content: flex-end; gap: 6px; }
  .contact svg { width: 12px; height: 12px; flex: none; }
</style>
</head>
<body>
<main class="canvas">

  <section class="card card--front" aria-label="Business card, front">
    <h1 class="brand-name">Ridgefell<span class="line-2">Construction</span></h1>
    <p class="since">Since 28 Years</p>
    <p class="tagline">Residential Contractor for Remodeling and Build</p>
  </section>

  <section class="card card--back" aria-label="Business card, back">
    <svg class="band" viewBox="0 0 580 330" width="580" height="330" aria-hidden="true">
      <polygon points="0,250 580,80 580,330 0,330" fill="var(--brand-blue)"/>
      <line x1="0" y1="266" x2="580" y2="96" stroke="var(--paper)" stroke-width="3"/>
    </svg>

    <h2 class="brand-name">Ridgefell<span class="line-2">Construction</span></h2>

    <div class="person">
      <p class="person__name">DANIEL HARROW</p>
      <p class="person__role">Managing Director</p>
      <p class="person__address">418, Harbour Lane<br>Westmere, 45316</p>
    </div>

    <ul class="contact">
      <li>044-318 270 546
        <svg viewBox="0 0 24 24" aria-label="Phone"><path fill="#fff" d="M6.6 10.8a15 15 0 0 0 6.6 6.6l2.2-2.2c.3-.3.7-.4 1-.2 1.1.4 2.3.6 3.6.6.6 0 1 .4 1 1V20c0 .6-.4 1-1 1A17 17 0 0 1 3 4c0-.6.4-1 1-1h3.5c.6 0 1 .4 1 1 0 1.3.2 2.5.6 3.6.1.3 0 .7-.2 1z"/></svg>
      </li>
      <li>info@ridgefell.com
        <svg viewBox="0 0 24 24" aria-label="Email"><rect x="2" y="5" width="20" height="14" fill="#fff"/><path d="M2 5l10 8 10-8" fill="none" stroke="#1f3d7f" stroke-width="2"/></svg>
      </li>
      <li>www.ridgefellbuild.com
        <svg viewBox="0 0 24 24" aria-label="Website"><circle cx="12" cy="12" r="10" fill="#fff"/><path d="M2 12h20M12 2c3 3 3 17 0 20M12 2c-3 3-3 17 0 20" fill="none" stroke="#1f3d7f" stroke-width="1.5"/></svg>
      </li>
    </ul>
  </section>

</main>
</body>
</html>
```